Business Card Design needed for start up company Halvora

In need of a new business card designed for a start up company based in Sydney, Halvora is a new start up innovative Company, our mission it to make property accessible for everyday Australian and to become the leading Real Estate platform in Australia. We want it to be fresh and clean.

Industry/Entity Type

Financial

Contact Information for Business Card

Section for Name
Section for Title

HALVORA - The Strength of Pooling
Mobile:
Direct:

Font styles to use
Sans Serif

Colors
33a6d7
0692cd
0255a3
ffffff

Requirements
Must have
• Logo, all business card details

```html
<!DOCTYPE html>
<html lang="en">
<head>
<meta charset="utf-8">
<title>Halvora Business Card</title>
<link rel="stylesheet" href="https://fonts.googleapis.com/css2?family=Open+Sans:wght@400;600;800&display=swap">
<style>
  :root {
    --sky: #33a6d7;
    --ocean: #0692cd;
    --navy: #0255a3;
    --deep-navy: #1c3f7a;
    --white: #ffffff;
    --paper: #f4f5f6;
    --backdrop: #3a3b3d;
  }
  * { margin: 0; padding: 0; box-sizing: border-box; }
  html, body { width: 1200px; height: 960px; overflow: hidden; }
  body {
    background: var(--backdrop);
    font-family: "Open Sans", Arial, sans-serif;
    display: flex;
    flex-direction: column;
    align-items: center;
    justify-content: center;
    gap: 56px;
  }
  .card {
    position: relative;
    width: 630px;
    height: 360px;
    border-radius: 4px;
    overflow: hidden;
    box-shadow: 0 10px 30px rgba(0,0,0,0.35);
  }
  /* Back side */
  .card-back {
    background: linear-gradient(135deg, var(--deep-navy), var(--navy));
    display: flex;
    flex-direction: column;
    align-items: center;
    justify-content: center;
  }
  .brand {
    display: flex;
    align-items: center;
    gap: 12px;
    font-weight: 800;
    letter-spacing: 1px;
  }
  .brand-dot { border-radius: 50%; flex: none; }
  .card-back .brand { color: var(--white); font-size: 58px; }
  .card-back .brand-dot { width: 62px; height: 62px; background: var(--white); }
  .tagline {
    margin-top: 42px;
    color: var(--white);
    font-size: 14px;
    letter-spacing: 0.3px;
  }
  /* Front side */
  .card-front { background: var(--paper); }
  .card-front .brand {
    position: absolute;
    left: 34px;
    top: 44px;
    color: var(--deep-navy);
    font-size: 54px;
  }
  .card-front .brand-dot { width: 58px; height: 58px; background: var(--ocean); }
  .wave { position: absolute; inset: 0; width: 100%; height: 100%; }
  .contact {
    position: absolute;
    right: 26px;
    top: 212px;
    text-align: right;
    color: var(--white);
  }
  .contact-name { font-weight: 600; font-size: 16px; line-height: 21px; letter-spacing: 0.5px; }
  .contact-title { font-size: 15px; line-height: 20px; margin-bottom: 6px; }
  .contact-line {
    display: flex;
    justify-content: flex-end;
    align-items: center;
    gap: 8px;
    font-size: 14px;
    line-height: 20px;
  }
  .contact-line svg { width: 13px; height: 13px; fill: var(--white); flex: none; }
  .address {
    position: absolute;
    left: 150px;
    bottom: 18px;
    color: var(--white);
    font-size: 14px;
  }
</style>
</head>
<body>
  <section class="card card-back" aria-label="Card back">
    <div class="brand"><span class="brand-dot"></span><span>HALVORA</span></div>
    <p class="tagline">The Strength of Pooling</p>
  </section>

  <section class="card card-front" aria-label="Card front">
    <svg class="wave" viewBox="0 0 630 360" preserveAspectRatio="none" aria-hidden="true">
      <defs>
        <linearGradient id="band" x1="0" y1="0" x2="1" y2="0">
          <stop offset="0" stop-color="#33a6d7"/>
          <stop offset="1" stop-color="#0692cd"/>
        </linearGradient>
      </defs>
      <path d="M0,190 C200,250 380,240 630,110 L630,360 L0,360 Z" fill="url(#band)"/>
      <path d="M0,197 C200,257 380,247 630,117" fill="none" stroke="#ffffff" stroke-width="2.5" opacity="0.85"/>
    </svg>

    <div class="brand"><span class="brand-dot"></span><span>HALVORA</span></div>

    <div class="contact">
      <p class="contact-name">MARA ELLISON</p>
      <p class="contact-title">CEO/FOUNDER</p>
      <p class="contact-line">612 480 3195
        <svg viewBox="0 0 16 16"><path d="M2 5c0-2 2-3 6-3s6 1 6 3v1h-3V4.5H5V6H2zM4 7h8l2 7H2z"/></svg></p>
      <p class="contact-line">614 725 0831
        <svg viewBox="0 0 16 16"><path d="M4 1h8v14H4zM5.5 2.5v9h5v-9z"/></svg></p>
      <p class="contact-line">mara@halvora.co
        <svg viewBox="0 0 16 16"><path d="M1 3h14v10H1zM2.5 4.5 8 9l5.5-4.5z"/></svg></p>
      <p class="contact-line">www.halvora.co
        <svg viewBox="0 0 16 16"><circle cx="8" cy="8" r="7"/></svg></p>
    </div>

    <p class="address">42 Harbour Street, Sydney, NSW 2000</p>
  </section>
</body>
</html>
```